New business Cards

We need some new cards that stand out. We love our logo and colour scheme but need to incorporate a quorva logo and tlm logo yet still keep our cards uncluttered and clean looking.
Our tag is Brisk Ledgerworks. Anywhere, Anytime.
The idea of the cards is to show authority in accounting and Quorva/ cloud software

Industry/Entity Type

Business

```html
<!DOCTYPE html>
<html lang="en">
<head>
<meta charset="utf-8">
<title>Tallow Accounting – business cards</title>
<link rel="stylesheet" href="https://fonts.googleapis.com/css2?family=Barlow:wght@400;500;600&family=PT+Serif&display=swap">
<style>
  :root{
    --stage:#35312f;
    --card:#ffffff;
    --brand-green:#6db554;
    --name-green:#3f8f3a;
    --ink:#111111;
    --mark-ink:#2b2b2b;
    --badge-neutral:#d9dcd6;
    --sans:"Barlow", Arial, sans-serif;
    --serif:"PT Serif", Georgia, serif;
  }
  *{box-sizing:border-box;margin:0;padding:0}
  html,body{width:1200px;height:1000px;overflow:hidden}
  body{background:var(--stage);position:relative;font-family:var(--sans)}

  .card{position:absolute;background:var(--card);box-shadow:0 4px 12px rgba(0,0,0,.45);overflow:hidden}

  .wordmark{display:flex;align-items:center;justify-content:center;gap:12px;color:var(--mark-ink);font-weight:600;white-space:nowrap}
  .wordmark .mark-square{background:var(--brand-green);flex:none}
  .wordmark .mark-name{line-height:1}

  /* Front */
  .card-front{left:70px;top:130px;width:420px;height:720px;text-align:center}
  .card-front .wordmark{position:absolute;left:0;right:0;top:150px}
  .card-front .mark-square{width:44px;height:44px}
  .card-front .mark-name{font-size:32px}

  .holder-name{position:absolute;top:352px;left:0;right:0;font-size:27px;font-weight:500;color:var(--name-green);letter-spacing:.5px}
  .holder-role{position:absolute;top:390px;left:0;right:0;font-size:22px;color:var(--ink)}
  .contact{position:absolute;left:0;right:0;font-size:20px;color:var(--ink);display:flex;justify-content:center;align-items:center;gap:7px}
  .contact svg{fill:var(--brand-green)}
  .contact-phone{top:438px}
  .contact-email{top:466px}

  .badge{position:absolute;background:var(--badge-neutral);border-radius:6px}
  .badge-tlm{left:32px;top:606px;width:142px;height:66px}
  .badge-quorva{left:242px;top:604px;width:144px;height:70px}

  /* Back */
  .card-back{left:550px;top:300px;width:600px;height:393px;text-align:center}
  .back-band{position:absolute;left:0;right:0;top:146px;bottom:0;background:var(--brand-green)}
  .logo-tile{position:absolute;left:180px;top:64px;width:240px;height:126px;background:var(--card);box-shadow:1px 2px 4px rgba(0,0,0,.3);display:flex;align-items:center;justify-content:center}
  .logo-tile .wordmark{gap:9px}
  .logo-tile .mark-square{width:28px;height:28px}
  .logo-tile .mark-name{font-size:22px}
  .tagline{position:absolute;top:280px;left:0;right:0;font-family:var(--serif);font-size:24px;color:#fff;letter-spacing:.5px;white-space:nowrap}
  .tagline .sep{margin:0 10px;font-size:16px;vertical-align:3px}
  .back-details{position:absolute;top:328px;left:0;right:0;color:#fff;font-size:20px;line-height:28px}
</style>
</head>
<body>

<section class="card card-front" aria-label="Business card front">
  <div class="wordmark">
    <span class="mark-square"></span>
    <span class="mark-name">Tallow Accounting</span>
  </div>

  <p class="holder-name">Maren Holt, TLM, RTX</p>
  <p class="holder-role">Partner</p>

  <p class="contact contact-phone">
    <svg width="14" height="14" viewBox="0 0 24 24" aria-hidden="true"><path d="M6.6 10.8a15.1 15.1 0 0 0 6.6 6.6l2.2-2.2c.3-.3.7-.4 1-.2 1.1.4 2.3.6 3.6.6.6 0 1 .4 1 1V20c0 .6-.4 1-1 1A17 17 0 0 1 3 4c0-.6.4-1 1-1h3.5c.6 0 1 .4 1 1 0 1.3.2 2.5.6 3.6.1.3 0 .7-.2 1z"/></svg>
    03 5550 1827
  </p>
  <p class="contact contact-email">
    <svg width="16" height="12" viewBox="0 0 16 12" aria-hidden="true"><path d="M0 0l8 6 8-6v12H0z"/><path d="M0 0h16L8 5.5z"/></svg>
    marenh@tallowacct.com.au
  </p>

  <div class="badge badge-tlm" role="img" aria-label="TLM member badge"></div>
  <div class="badge badge-quorva" role="img" aria-label="Quorva certified advisor badge"></div>
</section>

<section class="card card-back" aria-label="Business card back">
  <div class="back-band"></div>
  <div class="logo-tile">
    <div class="wordmark">
      <span class="mark-square"></span>
      <span class="mark-name">Tallow Accounting</span>
    </div>
  </div>
  <p class="tagline">BRISK LEDGERWORKS<span class="sep">•</span>ANYWHERE<span class="sep">•</span>ANYTIME</p>
  <p class="back-details">Elmvale Vic 3999<br>www.tallowacct.com.au</p>
</section>

</body>
</html>
```